Create a memorable Stationary for Security Software Company

Velbrantix is the worldwide leader in securing the Internet. Making Internet communications and critical data secure, reliable and available everywhere has been and continues to be our ongoing vision. We are committed to staying focused on real customer needs and to developing new and innovative security solutions that redefine the security landscape.

Industry/Entity Type

Internet

Font styles to use
Serif
Sans Serif
Script

Colors
0792cd
33a6d7
85cae6

```html
<!DOCTYPE html>
<html lang="en">
<head>
<meta charset="utf-8">
<title>Velbrantix Business Card</title>
<link rel="stylesheet" href="https://fonts.googleapis.com/css2?family=Open+Sans:wght@400;600;700&display=swap">
<style>
  :root {
    --brand-deep: #0792cd;
    --brand-mid: #33a6d7;
    --brand-light: #85cae6;
    --card-white: #ffffff;
    --pattern-tint: #e3f1f8;
    --ink: #2d3a40;
    --divider: #c9a58a;
    --page-bg: #eef1f3;
  }
  * { box-sizing: border-box; margin: 0; padding: 0; }
  html, body {
    width: 1200px; height: 1120px; overflow: hidden;
    background: var(--page-bg);
    font-family: "Open Sans", Arial, sans-serif;
  }
  .card {
    position: absolute; left: 160px;
    width: 880px; height: 503px;
    overflow: hidden;
    box-shadow: 0 6px 20px rgba(0,0,0,.15);
  }
  .card--front { top: 36px; background: var(--card-white); }
  .card--back { top: 581px; background: var(--brand-light); }

  .front__pattern {
    position: absolute; inset: 0;
    background: radial-gradient(circle at 50% 45%, var(--card-white) 0%, var(--pattern-tint) 75%);
  }
  .brand {
    position: absolute; display: flex; align-items: center; gap: 18px;
    color: var(--brand-deep); font-weight: 700; letter-spacing: .5px;
  }
  .brand__mark {
    border-radius: 50%; background: var(--brand-mid); flex: none;
  }
  .card--front .brand { left: 0; right: 0; top: 170px; justify-content: center; font-size: 62px; }
  .card--front .brand__mark { width: 70px; height: 70px; }
  .front__url {
    position: absolute; left: 0; right: 0; top: 330px; text-align: center;
    font-size: 26px; letter-spacing: 4px; color: var(--ink);
  }

  .card--back .brand { left: 70px; top: 150px; font-size: 50px; color: var(--brand-deep); }
  .card--back .brand__mark { width: 56px; height: 56px; background: var(--brand-deep); }
  .back__divider {
    position: absolute; left: 455px; top: 90px; width: 2px; height: 170px;
    background: var(--divider);
  }
  .contact {
    position: absolute; left: 485px; top: 84px; list-style: none;
    font-size: 21px; color: var(--ink); line-height: 1.45;
  }
  .contact li { display: flex; align-items: center; gap: 10px; }
  .contact svg { width: 18px; height: 18px; flex: none; fill: var(--brand-deep); }
  .contact .contact__address { padding-left: 28px; margin-top: 6px; line-height: 1.3; }
  .back__wave { position: absolute; left: 0; bottom: 0; width: 880px; height: 260px; }
  .holder {
    position: absolute; left: 200px; top: 390px; text-align: center; color: var(--card-white);
  }
  .holder__name { font-size: 27px; font-weight: 700; }
  .holder__title { font-size: 24px; }
</style>
</head>
<body>
  <section class="card card--front">
    <div class="front__pattern" role="img" aria-label="Faint repeated brand pattern across the card background"></div>
    <div class="brand"><span class="brand__mark"></span><span class="brand__name">Velbrantix</span></div>
    <p class="front__url">www.velbrantix.com</p>
  </section>

  <section class="card card--back">
    <div class="brand"><span class="brand__mark"></span><span class="brand__name">Velbrantix</span></div>
    <div class="back__divider"></div>
    <ul class="contact">
      <li><svg viewBox="0 0 24 24"><path d="M6.6 10.8a15 15 0 0 0 6.6 6.6l2.2-2.2c.3-.3.7-.4 1-.2 1.1.4 2.3.6 3.6.6.6 0 1 .4 1 1V20c0 .6-.4 1-1 1C10.6 21 3 13.4 3 4c0-.6.4-1 1-1h3.5c.6 0 1 .4 1 1 0 1.3.2 2.5.6 3.6.1.3 0 .7-.2 1z"/></svg>012-345-6789</li>
      <li><svg viewBox="0 0 24 24"><rect x="7" y="2" width="10" height="20" rx="2"/></svg>012-345-6789</li>
      <li><svg viewBox="0 0 24 24"><path d="M3 5h18v14H3zm2 2v.5l7 4.5 7-4.5V7z"/></svg>info@velbrantix.com</li>
      <li><svg viewBox="0 0 24 24"><circle cx="12" cy="12" r="9"/></svg>www.velbrantix.com</li>
      <li class="contact__address">Street Name, City Name<br>Zipcode-012345</li>
    </ul>
    <svg class="back__wave" viewBox="0 0 880 260" preserveAspectRatio="none" aria-hidden="true">
      <path d="M0 150 C250 95 520 150 880 30 L880 260 L0 260 Z" fill="#33a6d7"/>
      <path d="M0 165 C260 110 540 165 880 55 L880 260 L0 260 Z" fill="#ffffff" opacity=".7"/>
      <path d="M0 175 C270 120 560 175 880 70 L880 260 L0 260 Z" fill="#0792cd"/>
    </svg>
    <div class="holder">
      <p class="holder__name">Your Name</p>
      <p class="holder__title">Title</p>
    </div>
  </section>
</body>
</html>
```